Dunmore Roofing

Want a professional looking business card

Industry/Entity Type

Business

Contact Information for Business Card

Paul Dunmore ( Owner) paul@dunmoreroofing-example.com, www.dunmoreroofing-example.com, Adress: 4172 Township road 43 Plantagenet,ON K9X4T2

```html
<!DOCTYPE html>
<html lang="en">
<head>
<meta charset="utf-8">
<title>Dunmore Roofing – Business Card</title>
<link href="https://fonts.googleapis.com/css2?family=Open+Sans:wght@400;600;700&display=swap" rel="stylesheet">
<style>
  :root {
    --brand-blue: #1c4587;
    --accent-grey: #6e6e6e;
    --text-grey: #5a5a5a;
    --rule-grey: #c9c9c9;
    --paper: #ffffff;
    --backdrop: #4a4a4a;
  }
  html, body {
    margin: 0;
    width: 1200px;
    height: 900px;
    overflow: hidden;
    background: var(--backdrop);
    font-family: "Open Sans", Arial, sans-serif;
  }
  .canvas {
    position: relative;
    width: 1200px;
    height: 900px;
  }
  .card {
    position: absolute;
    width: 540px;
    height: 310px;
    top: 295px;
    overflow: hidden;
    box-shadow: 0 10px 30px rgba(0,0,0,.35);
  }

  /* Front (blue) */
  .card--front {
    left: 50px;
    background: var(--brand-blue);
  }
  .front__map {
    position: absolute;
    left: 90px;
    top: 25px;
    width: 420px;
    height: 260px;
    border-radius: 40px;
    background: radial-gradient(ellipse at center, rgba(255,255,255,.07), rgba(255,255,255,0) 70%);
  }
  .front__name {
    position: absolute;
    left: 0;
    right: 0;
    top: 110px;
    display: flex;
    justify-content: center;
    align-items: center;
    gap: 12px;
    color: var(--paper);
    font-weight: 700;
    font-size: 34px;
    letter-spacing: 3px;
    text-transform: uppercase;
    white-space: nowrap;
  }
  .front__mark {
    width: 18px;
    height: 18px;
    background: var(--paper);
  }
  .front__web {
    position: absolute;
    left: 0;
    right: 0;
    bottom: 42px;
    margin: 0;
    text-align: center;
    color: var(--paper);
    font-size: 17px;
  }

  /* Back (white) */
  .card--back {
    left: 610px;
    background: var(--paper);
  }
  .back__bands {
    position: absolute;
    inset: 0;
  }
  .back__brand {
    position: absolute;
    left: 20px;
    top: 146px;
    display: flex;
    align-items: center;
    gap: 8px;
    color: var(--brand-blue);
    font-weight: 700;
    font-size: 18px;
    letter-spacing: 1.5px;
    text-transform: uppercase;
    white-space: nowrap;
  }
  .back__mark {
    width: 13px;
    height: 13px;
    background: var(--brand-blue);
    flex: none;
  }
  .back__divider {
    position: absolute;
    left: 290px;
    top: 100px;
    width: 1px;
    height: 120px;
    background: var(--rule-grey);
  }
  .contact {
    position: absolute;
    left: 303px;
    top: 100px;
    width: 230px;
    color: var(--text-grey);
    font-size: 11.5px;
    line-height: 1.45;
  }
  .contact__name {
    color: var(--brand-blue);
    font-weight: 700;
    font-size: 14px;
    margin: 0;
  }
  .contact__role {
    margin: 0 0 4px;
  }
  .contact__address {
    margin: 0 0 4px;
    font-style: normal;
  }
  .contact__line {
    display: flex;
    align-items: center;
    gap: 6px;
    margin: 1px 0;
    white-space: nowrap;
  }
  .contact__icon {
    width: 14px;
    height: 14px;
    flex: none;
  }
</style>
</head>
<body>
<main class="canvas">

  <section class="card card--front" aria-label="Card front">
    <div class="front__map" role="img" aria-label="Faint dotted world map in the background"></div>
    <div class="front__name"><span class="front__mark"></span>Dunmore Roofing</div>
    <p class="front__web">www.dunmoreroofing-example.com</p>
  </section>

  <section class="card card--back" aria-label="Card back">
    <svg class="back__bands" viewBox="0 0 540 310" preserveAspectRatio="none" aria-hidden="true">
      <polygon points="0,0 540,0 540,62 160,14 0,14" fill="var(--brand-blue)"/>
      <polygon points="160,14 540,62 540,78 170,20" fill="var(--accent-grey)"/>
      <polygon points="300,310 540,220 540,310" fill="var(--brand-blue)"/>
    </svg>

    <div class="back__brand"><span class="back__mark"></span>Dunmore Roofing</div>
    <div class="back__divider"></div>

    <div class="contact">
      <p class="contact__name">Paul Dunmore</p>
      <p class="contact__role">Owner</p>
      <address class="contact__address">4172 Township road 43,<br>Alderbrook, ON K9X4T2</address>
      <p class="contact__line">
        <svg class="contact__icon" viewBox="0 0 14 14" aria-hidden="true"><circle cx="7" cy="7" r="7" fill="var(--brand-blue)"/><path d="M4.6 3.6l1.3 1.4-.7 1a4.2 4.2 0 0 0 2.8 2.8l1-.7 1.4 1.3-.9 1.1C6.6 10.3 3.7 7.4 3.5 4.5z" fill="#fff"/></svg>
        (613) 555-0147
      </p>
      <p class="contact__line">
        <svg class="contact__icon" viewBox="0 0 14 14" aria-hidden="true"><circle cx="7" cy="7" r="7" fill="var(--brand-blue)"/><rect x="3.5" y="4.5" width="7" height="5" fill="none" stroke="#fff" stroke-width="1"/><path d="M3.5 4.5L7 7.3l3.5-2.8" fill="none" stroke="#fff" stroke-width="1"/></svg>
        paul@dunmoreroofing-example.com
      </p>
      <p class="contact__line">
        <svg class="contact__icon" viewBox="0 0 14 14" aria-hidden="true"><circle cx="7" cy="7" r="7" fill="var(--brand-blue)"/><circle cx="7" cy="7" r="3.6" fill="none" stroke="#fff" stroke-width="1"/><path d="M3.4 7h7.2M7 3.4c-1.6 2-1.6 5.2 0 7.2M7 3.4c1.6 2 1.6 5.2 0 7.2" fill="none" stroke="#fff" stroke-width=".8"/></svg>
        www.dunmoreroofing-example.com
      </p>
    </div>
  </section>

</main>
</body>
</html>
```